A website for Kovadrel Limited

We need a new and modern website for our company. We are engineering consultants and contractors (EPC) in the oil and gas industry and building services industry.
What we do:
Engineering, procurement, construction
Automation (safety and process)
Non-destructive testing
Training
We have an existing website and the content can be referred from there since we are remaking the website
For more information visit Kovadrel Limited Kenya

```html
<!DOCTYPE html>
<html lang="en">
<head>
<meta charset="utf-8">
<title>Kovadrel Limited</title>
<link rel="stylesheet" href="https://fonts.googleapis.com/css2?family=Montserrat:wght@500;600;700;800&family=Lato:wght@400;700&display=swap">
<style>
:root{
  --orange:#e8793f;
  --orange-dark:#d9652d;
  --red:#d9473f;
  --red-dark:#a8372a;
  --ink:#1b1b1b;
  --white:#ffffff;
  --muted:#555;
}
*{box-sizing:border-box;margin:0;padding:0}
html,body{width:1200px;height:2854px;overflow:hidden;background:#fff}
body{position:relative;font-family:"Lato",sans-serif;color:var(--ink)}
.abs{position:absolute}
.caps{font-family:"Montserrat",sans-serif;font-variant:small-caps;font-weight:700}

/* header */
.topbar{left:410px;top:0;width:790px;height:53px;background:var(--orange-dark);border-bottom-left-radius:60px 53px;color:#fff;font-family:"Montserrat",sans-serif;font-weight:700;font-size:15px;letter-spacing:1px;display:flex;align-items:center;gap:34px;padding-left:58px}
.topbar .item{display:flex;align-items:center;gap:10px}
.topbar .ic{width:30px;height:30px;border:2px solid #fff;border-radius:50%;display:flex;align-items:center;justify-content:center}
.brand{left:112px;top:10px;display:flex;align-items:center;gap:10px}
.brand .dot{width:100px;height:100px;border-radius:50%;border:3px solid var(--red-dark);background:var(--orange)}
.brand .name{font-family:"Montserrat",sans-serif;font-weight:500;font-size:29px;line-height:36px;color:var(--orange-dark)}
.nav{top:72px;left:443px;display:flex;gap:50px;font-family:"Montserrat",sans-serif;font-weight:600;font-size:15px;letter-spacing:.6px}
.nav .active{color:var(--orange-dark);text-decoration:underline;text-underline-offset:4px}
.cta{left:943px;top:66px;width:146px;height:42px;border-radius:20px;background:linear-gradient(#f29a50,var(--orange-dark));font-family:"Montserrat",sans-serif;font-weight:700;font-size:16px;display:flex;align-items:center;justify-content:center;color:#2a1306;box-shadow:2px 3px 4px rgba(0,0,0,.25)}

/* hero */
.hero{left:0;top:120px;width:1200px;height:590px;background:linear-gradient(180deg,#3c4a78 0%,#8a6f98 25%,#c88a76 40%,#3a3f5a 60%,#1d2338 80%,#2e2a35 100%)}
.hero-title{top:172px;width:1200px;text-align:center;color:#fff;font-family:"Montserrat",sans-serif;font-weight:800;font-size:44px;letter-spacing:1.5px;text-shadow:2px 3px 5px rgba(0,0,0,.55)}
.hero-sub{top:228px;left:280px;width:640px;text-align:center;color:#fff;font-weight:700;font-size:14.5px;line-height:26px;text-shadow:1px 1px 3px rgba(0,0,0,.6)}
.pill{background:#fff;border-radius:24px;color:var(--red);font-size:18px;display:flex;align-items:center;justify-content:center;box-shadow:0 3px 6px rgba(0,0,0,.2)}

/* section titles */
.section-title{width:1200px;display:flex;justify-content:center;align-items:center;gap:12px;font-size:42px;color:var(--ink)}
.mini-dot{width:44px;height:44px;border-radius:50%;background:var(--orange);border:2px solid var(--red-dark)}

/* service cards */
.card{width:295px;border-radius:0 0 148px 148px;color:#fff;text-align:center;box-shadow:0 6px 12px rgba(0,0,0,.18)}
.card.red{background:var(--red);height:412px;top:799px}
.card.orange{background:var(--orange);height:491px;top:799px;overflow:hidden}
.card .photo{height:186px;background:linear-gradient(135deg,#263a55,#6a7f94 45%,#d28a3b 70%,#2a2f3e)}
.icon-ring{width:120px;height:120px;border-radius:50%;background:#fff;border:4px solid rgba(255,255,255,.6);box-shadow:0 0 0 4px var(--red);margin:29px auto 0;display:flex;align-items:center;justify-content:center}
.card h3{font-family:"Montserrat",sans-serif;font-variant:small-caps;font-weight:800;font-size:18px;line-height:26px;margin-top:18px}
.card p{font-size:15.5px;line-height:26px;padding:0 22px;margin-top:10px}
.card .go{margin:12px auto 0;width:24px;height:24px}
.slider-arrow{width:34px;height:34px;border-radius:50%;background:var(--red-dark);top:988px;display:flex;align-items:center;justify-content:center}

/* about */
.about{left:0;top:1379px;width:1200px;height:501px;background:linear-gradient(90deg,#b5402f,#c24a34 45%,#b8432f 100%);overflow:hidden}
.about-title{left:520px;top:1440px;color:#fff;font-size:41px;display:flex;align-items:center;gap:12px}
.about-text{left:565px;top:1506px;width:530px;color:#fff;font-size:13.6px;line-height:25.7px;text-align:center}

/* products */
.product{width:233px;height:233px;top:2001px;border-radius:50%;border:4px solid var(--red);overflow:hidden;position:absolute}
.product .band{position:absolute;left:0;right:0;bottom:0;height:92px;color:#fff;font-family:"Montserrat",sans-serif;font-weight:700;font-size:17px;letter-spacing:.5px;display:flex;align-items:flex-end;justify-content:center;padding-bottom:18px}

/* footer */
.footer-text{color:#fff}
.foot-h{font-family:"Montserrat",sans-serif;font-weight:700;font-size:19px;letter-spacing:.5px;color:#fff}
.foot-list{list-style:none;color:#fff;font-size:15.5px}
.foot-list li{height:34.5px;display:flex;align-items:center;gap:10px}
.bullet{width:13px;height:13px;border-radius:50%;background:#fff;position:relative}
.bullet::after{content:"";position:absolute;left:3px;top:4px;border:3px solid transparent;border-left:5px solid #000;border-right:0}
.social{width:30px;height:30px;border-radius:50%;background:var(--red);top:2668px}
.contact-row{display:flex;gap:16px;color:#fff;font-size:15.5px;line-height:27px;align-items:flex-start}
.contact-ic{flex:none;width:30px;height:30px;border-radius:50%;background:var(--red);display:flex;align-items:center;justify-content:center;margin-top:-1px}
</style>
</head>
<body>

<!-- header -->
<div class="abs topbar">
  <div class="item"><span class="ic"><svg width="14" height="14" viewBox="0 0 24 24"><path fill="#fff" d="M6.6 10.8a15 15 0 0 0 6.6 6.6l2.2-2.2c.3-.3.7-.4 1-.2 1.1.4 2.3.6 3.6.6.6 0 1 .4 1 1V20c0 .6-.4 1-1 1A17 17 0 0 1 3 4c0-.6.4-1 1-1h3.5c.6 0 1 .4 1 1 0 1.3.2 2.5.6 3.6.1.3 0 .7-.2 1z"/></svg></span>PHONE: +254 700 555 012</div>
  <span>|</span>
  <div class="item"><span class="ic"><svg width="14" height="12" viewBox="0 0 24 18"><path fill="#fff" d="M0 0h24v18H0z"/><path d="M0 0l12 9L24 0" fill="none" stroke="#d9652d" stroke-width="2"/></svg></span>MAIL: INFO@KOVADREL.EXAMPLE</div>
</div>
<div class="abs brand"><div class="dot"></div><div class="name">Kovadrel<br>Limited</div></div>
<nav class="abs nav"><span class="active">HOME</span><span>ABOUT</span><span>WHAT WE DO</span><span>PRODUCT</span></nav>
<div class="abs cta">CONTACT US</div>

<!-- hero -->
<div class="abs hero" role="img" aria-label="Oil refinery lit at dusk under a purple sky"></div>
<svg class="abs" style="left:0;top:480px" width="1200" height="240" viewBox="0 0 1200 240">
  <path d="M0 35 Q600 390 1200 35 L1200 240 L0 240 Z" fill="#fff"/>
  <path d="M0 44 Q40 60 85 78" stroke="#a8372a" stroke-width="9" fill="none"/>
  <path d="M205 140 Q600 290 1200 40" stroke="#a8372a" stroke-width="9" fill="none"/>
</svg>
<div class="abs hero-title">WELCOME TO KOVADREL LIMITED</div>
<div class="abs hero-sub">Kovadrel undertakes Design, Supply, Installation and Commissioning of LPG and Petroleum systems including LPG Reticulated Systems (piped gas).</div>
<div class="abs pill caps" style="left:514px;top:290px;width:172px;height:51px">Shop now</div>

<!-- services -->
<div class="abs section-title caps" style="top:728px"><span class="mini-dot"></span>Our Services</div>

<div class="abs slider-arrow" style="left:44px"><svg width="12" height="14" viewBox="0 0 12 14"><path d="M8 2L3 7l5 5" stroke="#fff" stroke-width="2.5" fill="none"/></svg></div>
<div class="abs slider-arrow" style="left:1124px"><svg width="12" height="14" viewBox="0 0 12 14"><path d="M4 2l5 5-5 5" stroke="#fff" stroke-width="2.5" fill="none"/></svg></div>

<div class="abs card red" style="left:112px">
  <div class="icon-ring"><svg width="60" height="60" viewBox="0 0 60 60" fill="none" stroke="#d9473f" stroke-width="3"><circle cx="22" cy="36" r="11"/><circle cx="22" cy="36" r="4"/><circle cx="42" cy="20" r="8"/><circle cx="42" cy="20" r="3"/></svg></div>
  <h3>Engineering, Procurement,<br>Construction</h3>
  <p>Oil companies (both multinationals and local), government agencies, manufacturing companies, agricultural institutions, and the building services industry.</p>
  <svg class="go" viewBox="0 0 24 24"><circle cx="12" cy="12" r="11" fill="#fff"/><path d="M7 12h9M12 7l5 5-5 5" stroke="#d9473f" stroke-width="2.5" fill="none"/></svg>
</div>

<div class="abs card orange" style="left:445px">
  <div class="photo" role="img" aria-label="Engineer in a hard hat working at an automation control screen"></div>
  <div class="icon-ring" style="margin-top:-64px;box-shadow:0 0 0 4px var(--orange);position:relative"><svg width="60" height="60" viewBox="0 0 60 60" fill="none" stroke="#e8793f" stroke-width="3"><rect x="8" y="12" width="36" height="26" rx="2"/><path d="M20 44h12"/><circle cx="44" cy="40" r="9"/><circle cx="44" cy="40" r="3"/></svg></div>
  <h3 style="margin-top:12px">Automation<br>(Safety and Process)</h3>
  <p>Oil companies (both multinationals and local), government agencies, manufacturing companies, agricultural institutions,</p>
  <svg class="go" viewBox="0 0 24 24"><circle cx="12" cy="12" r="11" fill="#fff"/><path d="M7 12h9M12 7l5 5-5 5" stroke="#e8793f" stroke-width="2.5" fill="none"/></svg>
</div>

<div class="abs card red" style="left:793px">
  <div class="icon-ring"><svg width="60" height="60" viewBox="0 0 60 60" fill="none" stroke="#d9473f" stroke-width="3"><rect x="10" y="10" width="34" height="40" rx="2"/><path d="M16 22h6M26 22h12M16 32h6M26 32h10M16 42h6"/><circle cx="44" cy="40" r="9"/><path d="M40 40l3 3 5-6"/></svg></div>
  <h3>Non-destructive<br>Testing</h3>
  <p>Oil companies (both multinationals and local), government agencies, manufacturing companies, agricultural institutions, and the building services industry.</p>
  <svg class="go" viewBox="0 0 24 24"><circle cx="12" cy="12" r="11" fill="#fff"/><path d="M7 12h9M12 7l5 5-5 5" stroke="#d9473f" stroke-width="2.5" fill="none"/></svg>
</div>

<!-- about -->
<div class="abs about" role="img" aria-label="Refinery storage tanks and pipework in a red tint">
  <div class="abs" style="left:-40px;top:0;width:500px;height:501px;border-radius:50%;background:#8e2c22"></div>
</div>
<div class="abs about-title caps"><span class="mini-dot" style="background:#fff;border-color:#fff"></span>About Kovadrel Limited</div>
<div class="abs about-text">
  <p>Kovadrel undertakes Design, Supply, Installation and Commissioning of LPG and Petroleum systems including LPG Reticulated Systems (piped gas). We also do LPG tank revalidation and recertification.Our clients include: Oil companies (both multinationals and local), government agencies, manufacturing companies, agricultural institutions, and the building services industry.</p>
  <p style="margin-top:25px">Kovadrel was incorporated in 2010 with the huge potential of the LPG and Petroleum market in Eastern and Central Africa in mind. We have provided and continue to provide the LPG and Petroleum Technical industry with innovative and cost-effective services.</p>
</div>
<div class="abs pill caps" style="left:745px;top:1757px;width:171px;height:51px">Read More</div>

<!-- products -->
<div class="abs section-title caps" style="top:1926px"><span class="mini-dot"></span>Our Products</div>

<div class="product" style="left:82px;border-color:var(--orange)">
  <div style="position:absolute;inset:0;background:linear-gradient(135deg,#5b636e,#c9a38a 50%,#3c4350)" role="img" aria-label="Hand holding an LPG fuel nozzle"></div>
  <div class="band" style="background:var(--orange)">LPG</div>
</div>
<div class="product" style="left:350px">
  <div style="position:absolute;inset:0;background:linear-gradient(180deg,#4b5d8a,#c88a58 55%,#1d2a45)" role="img" aria-label="Offshore petroleum platform lit at night"></div>
  <div class="band" style="background:var(--red)">PETROLEUM</div>
</div>
<div class="product" style="left:617px">
  <div style="position:absolute;inset:0;background:linear-gradient(135deg,#9fb1c4,#e0a040 45%,#5a6a7c)" role="img" aria-label="Robotic arms on an automated production line"></div>
  <div class="band" style="background:var(--orange)">AUTOMATION</div>
</div>
<div class="product" style="left:885px">
  <div style="position:absolute;inset:0;background:linear-gradient(135deg,#e7a35a,#c94a2b 45%,#3a3e4a)" role="img" aria-label="Firefighters spraying water at a blaze"></div>
  <div class="band" style="background:var(--red)">FIRE FIGHTING</div>
</div>

<!-- footer -->
<svg class="abs" style="left:0;top:2270px" width="1200" height="584" viewBox="0 0 1200 584">
  <path d="M0 210 Q600 -160 1200 210 L1200 584 L0 584 Z" fill="#000"/>
  <path d="M0 200 Q420 -80 990 90" stroke="#a8372a" stroke-width="9" fill="none"/>
  <path d="M1115 145 Q1160 168 1200 195" stroke="#a8372a" stroke-width="9" fill="none"/>
</svg>
<div class="abs" style="left:482px;top:2383px;display:flex;align-items:center;gap:10px">
  <div style="width:96px;height:96px;border-radius:50%;border:4px solid #fff"></div>
  <div style="font-family:Montserrat,sans-serif;font-weight:500;font-size:27px;line-height:34px;color:#fff">Kovadrel<br>Limited</div>
</div>
<div class="abs" style="left:111px;top:2505px;width:978px;height:1px;background:#666"></div>

<div class="abs foot-h" style="left:112px;top:2543px">KOVADREL LIMITED</div>
<div class="abs footer-text" style="left:111px;top:2574px;width:290px;font-size:13.8px;line-height:25.7px">We have provided and continue to provide the LPG and Petroleum Technical industry with innovative and cost-effective services.</div>
<div class="abs social" style="left:112px"></div>
<div class="abs social" style="left:164px"></div>
<div class="abs social" style="left:217px"></div>
<div class="abs social" style="left:269px"></div>

<div class="abs foot-h" style="left:469px;top:2543px">QUICK LINKS</div>
<ul class="abs foot-list" style="left:469px;top:2580px">
  <li><span class="bullet"></span>Home</li><li><span class="bullet"></span>About</li><li><span class="bullet"></span>Services</li><li><span class="bullet"></span>Products</li><li><span class="bullet"></span>Contact Us</li>
</ul>

<div class="abs foot-h" style="left:670px;top:2543px">HELP LINKS</div>
<ul class="abs foot-list" style="left:670px;top:2580px">
  <li><span class="bullet"></span>FAQ</li><li><span class="bullet"></span>Terms of use</li><li><span class="bullet"></span>Privacy Policy</li><li><span class="bullet"></span>Support Links</li><li><span class="bullet"></span>Conditions</li>
</ul>

<div class="abs foot-h" style="left:872px;top:2543px">CONTACT US</div>
<div class="abs" style="left:872px;top:2586px;width:300px">
  <div class="contact-row"><span class="contact-ic"><svg width="12" height="16" viewBox="0 0 12 16"><path d="M6 0a6 6 0 0 0-6 6c0 4 6 10 6 10s6-6 6-10a6 6 0 0 0-6-6z" fill="#fff"/><circle cx="6" cy="6" r="2" fill="#d9473f"/></svg></span><span>Larkfield Plaza, Next to Riverside Centre, Mwembe, Suite 14,</span></div>
  <div class="contact-row" style="margin-top:18px"><span class="contact-ic"><svg width="14" height="14" viewBox="0 0 24 24"><path fill="#fff" d="M6.6 10.8a15 15 0 0 0 6.6 6.6l2.2-2.2c.3-.3.7-.4 1-.2 1.1.4 2.3.6 3.6.6.6 0 1 .4 1 1V20c0 .6-.4 1-1 1A17 17 0 0 1 3 4c0-.6.4-1 1-1h3.5c.6 0 1 .4 1 1 0 1.3.2 2.5.6 3.6.1.3 0 .7-.2 1z"/></svg></span><span>+254 700 555 034</span></div>
  <div class="contact-row" style="margin-top:24px"><span class="contact-ic"><svg width="14" height="11" viewBox="0 0 24 18"><path fill="#fff" d="M0 0h24v18H0z"/><path d="M0 0l12 9L24 0" fill="none" stroke="#d9473f" stroke-width="2"/></svg></span><span>info@kovadrel.example</span></div>
</div>

<div class="abs" style="left:111px;top:2780px;width:978px;height:1px;background:#666"></div>
<div class="abs" style="top:2809px;width:1200px;text-align:center;color:#fff;font-size:15.5px">Copyrights@2023.Kovadrel Limited.All Rights Reserved</div>

</body>
</html>
```